QRV Advisors needs a web site

We need a web site for www.qrvadvisors-example.com. QRV is a mergers and acquisition consulting company that focuses our buyer and seller services on logistics companies. We help put companies together, and help with legal and financial due diligence. We want the web site to express our service and show the logistics components. We want personalized images versus pictures of trucks and airplanes.

Our new logo uses Burgandy and grey colors. Image attached. We are not in to bold, big letters...classy, artistic, low key preferred. Confidentiality, experience, professional are what we want to express on the site.

All we expect for the first part of this project is a home page, and one subpage.  We are budgeting other funds for the technical aspects of the web site

Reason: All that I'm seeing so far is trucks, forklifts and planes. We are a legal mergers and acquisitions firm that focus on logistics. I like some of the images to say logistics, but really want it say legal, financial, and putting companies together. Will pay extra for the sub page if someone can impress us with a home page.

Reason: Swamped with another project at the moment...will work on this over the weekend and provide designer feedback and select final design by Tuesday

```html
<!DOCTYPE html>
<html lang="en">
<head>
<meta charset="utf-8">
<title>QRV Advisors</title>
<link href="https://fonts.googleapis.com/css2?family=Open+Sans:wght@300;400;600;700&family=Raleway:wght@400&display=swap" rel="stylesheet">
<style>
:root{
  --burgundy:#9b0a2e;
  --burgundy-dark:#7d0824;
  --grey:#4a4a4a;
  --text-soft:#9a9a9a;
  --paper:#efe9e2;
  --panel:#fbfbfa;
  --rule:#7b7fa6;
  --footer:#2f2f2f;
  --footer-text:#9d9d9d;
  --link:#3c4a7a;
}
*{box-sizing:border-box;margin:0;padding:0}
html,body{width:1104px;height:1200px;overflow:hidden}
body{font-family:"Open Sans",sans-serif;background:var(--paper);color:var(--grey);position:relative}
.abs{position:absolute}

.site-header{position:absolute;left:0;top:0;width:1104px;height:100px;background:#fff}
.brand{left:166px;top:30px;display:flex;align-items:center;gap:12px}
.brand-mark{font-size:40px;font-weight:300;color:var(--burgundy);letter-spacing:2px;line-height:1}
.brand-divider{width:1px;height:46px;background:var(--grey)}
.brand-name{font-size:15px;font-weight:300;color:var(--burgundy);letter-spacing:1px;text-transform:uppercase;line-height:1.1;width:100px}
.call{right:164px;top:20px;font-size:12px;color:var(--grey)}
.call strong{font-size:18px;font-weight:600;color:var(--burgundy);margin-left:2px}
.search{left:648px;top:54px;width:148px;height:22px;border:1px solid #ccc;font-size:10px;color:#888;padding:4px 6px;display:flex;justify-content:space-between;align-items:center}
.socials{left:807px;top:51px;display:flex;gap:5px}
.socials span{width:30px;height:30px;border-radius:50%;background:#b9c0cc}

.main-nav{position:absolute;left:0;top:100px;width:1104px;height:33px;background:var(--burgundy)}
.main-nav ul{list-style:none;display:flex;position:absolute;left:151px;top:0;height:33px}
.main-nav li{color:#fff;font-size:12px;padding:0 16px;line-height:33px;border-right:1px solid var(--burgundy-dark)}
.main-nav li:last-child{border-right:0}

.hero{position:absolute;left:0;top:133px;width:1104px;height:422px;background:linear-gradient(180deg,#d8e3ea 0%,#c9d5dd 55%,#3b57a8 72%,#2d4597 85%,#c0694c 100%)}
.hero-caption{position:absolute;left:175px;top:115px;width:412px;height:202px;background:rgba(20,18,18,.88);padding:12px 10px}
.hero-caption h1{font-family:"Raleway",sans-serif;font-weight:400;font-size:28px;color:#fff;letter-spacing:.3px;padding-bottom:6px;border-bottom:1px dashed #ddd;margin:0 10px 0 0}
.hero-caption h2{font-size:17px;font-weight:400;color:#fff;margin:10px 0 10px 6px}
.hero-caption p{font-size:10px;line-height:20px;color:#fff;margin-left:6px;width:360px}
.btn-hero{display:inline-block;margin:8px 0 0 4px;background:var(--burgundy);color:#fff;font-size:11px;padding:9px 25px;border-radius:3px}
.dots{left:577px;top:523px;display:flex;gap:4px}
.dots span{width:10px;height:10px;border-radius:50%;background:#fff}
.dots span:first-child{background:var(--burgundy)}
.hero-next{left:978px;top:320px}

.features{position:absolute;left:166px;top:555px;width:772px;height:238px;background:var(--panel);border-bottom:5px solid var(--rule)}
.feature{position:absolute;top:18px;width:229px;height:210px}
.feature .thumb{width:229px;height:114px;border-radius:2px}
.feature h3{font-size:11.5px;font-weight:400;color:var(--burgundy);margin:11px 0 6px;letter-spacing:-.2px}
.feature p{font-size:9px;line-height:13.5px;color:var(--text-soft);max-height:41px;overflow:hidden}
.feature p.tight{font-size:8px;letter-spacing:-.15px}
.feature a{position:absolute;left:0;top:193px;font-size:10px;color:var(--link);text-decoration:none;line-height:1}

.logistics{position:absolute;left:166px;top:807px;width:772px;height:186px;background:var(--panel);border-radius:3px;box-shadow:0 0 3px rgba(0,0,0,.08)}
.logistics h2{position:absolute;left:14px;top:20px;font-size:15px;font-weight:400;color:var(--grey);letter-spacing:-.3px}
.logistics hr{position:absolute;left:14px;top:48px;width:744px;border:0;border-top:1px solid #e6e3e0}
.route{position:absolute;top:60px;width:215px}
.route h3{font-size:12px;font-weight:400;color:var(--burgundy);letter-spacing:-.3px}
.route p{font-size:8.5px;line-height:14px;color:var(--text-soft);margin:7px 0 9px}
.btn-small{display:inline-block;background:var(--burgundy);color:#fff;font-size:10px;padding:4px 8px;border-radius:2px}

.site-footer{position:absolute;left:0;top:1010px;width:1104px;height:190px;background:var(--footer);color:var(--footer-text)}
.site-footer h4{font-size:13px;font-weight:600;color:#fff;margin-bottom:10px}
.site-footer p{font-size:9.5px;line-height:12.3px}
.foot-col{position:absolute;top:17px}
.foot-brand{left:816px;top:34px;text-align:center;width:120px}
.foot-brand .mark{font-size:38px;font-weight:300;color:#bdbdbd;letter-spacing:3px;line-height:1}
.foot-brand .name{font-size:10px;color:#9a9a9a;margin-top:6px}
.copyright{left:166px;top:130px;font-size:9.5px}
.foot-social{left:821px;top:125px;display:flex;gap:6px}
.foot-social span{width:24px;height:24px;background:#6b6b6b;border-radius:2px}
</style>
</head>
<body>

<header class="site-header">
  <div class="brand abs">
    <span class="brand-mark">QRV</span>
    <span class="brand-divider"></span>
    <span class="brand-name">QRV Advisors</span>
  </div>
  <div class="call abs">Call: <strong>555.014.2290</strong></div>
  <div class="search abs">Search
    <svg width="10" height="10" viewBox="0 0 10 10"><circle cx="4" cy="4" r="3" fill="none" stroke="#999" stroke-width="1.2"/><line x1="6.3" y1="6.3" x2="9" y2="9" stroke="#999" stroke-width="1.2"/></svg>
  </div>
  <div class="socials abs"><span></span><span></span><span></span><span></span></div>
</header>

<nav class="main-nav">
  <ul>
    <li>THE QRV</li><li>LOGISTICS</li><li>MARKET ANALYSIS</li><li>COMMUNITY</li><li>MEDIA</li><li>ABOUT US</li><li>TEXAS TEAM</li><li>CONTACT US</li>
  </ul>
</nav>

<section class="hero" role="img" aria-label="Cargo ship loaded with containers at sea under a pale sky">
  <div class="hero-caption">
    <h1>QRV ADVISORS</h1>
    <h2>Lorest Nesto Magnust Quist Opus</h2>
    <p>Phasellus convallis massa vitae purus tincidunt sed faucibus ligula dignissim. Suspendisse ac velit congue eros faucibus mollis ornare eu diam. Cras vehicula bibendum velit in venenatis.</p>
    <span class="btn-hero">LEARN MORE</span>
  </div>
  <svg class="hero-next abs" width="16" height="28" viewBox="0 0 16 28"><polyline points="3,3 13,14 3,25" fill="none" stroke="#e6e6e6" stroke-width="4"/></svg>
  <div class="dots abs"><span></span><span></span><span></span></div>
</section>

<section class="features">
  <article class="feature" style="left:23px">
    <div class="thumb" role="img" aria-label="Container ship under way" style="background:linear-gradient(160deg,#3b5d78,#9aa9b4 55%,#d9dde0)"></div>
    <h3>Daryage Calculator</h3>
    <p class="tight">Lacus fermentum ultrices ut eu turpis. Quisque sodales turpis ut risus dignissim non auctor velit malesuada. Nunc tristique mi ac turpis placerat quis sollicitudin</p>
    <a>Read More</a>
  </article>
  <article class="feature" style="left:271px">
    <div class="thumb" role="img" aria-label="Truck loading freight beside a cargo aircraft" style="background:linear-gradient(160deg,#d6dbe0,#7f8a96 50%,#3c4550)"></div>
    <h3>Interactive Trade Map</h3>
    <p>Lacus fermentum ultrices ut eu turpis. Quisque sodales turpis ut risus dignissim non auctor velit malesuada.</p>
    <a>Read More</a>
  </article>
  <article class="feature" style="left:518px">
    <div class="thumb" role="img" aria-label="White delivery truck in motion" style="background:linear-gradient(150deg,#b8c0c2,#e8ebeb 45%,#4b5353)"></div>
    <h3>SIte Map</h3>
    <p>Lacus fermentum ultrices ut eu turpis. Quisque sodales turpis ut risus dignissim non auctor velit malesuada.</p>
    <a>Read More</a>
  </article>
</section>

<section class="logistics">
  <h2>Logistics</h2>
  <hr>
  <div class="route" style="left:14px"><h3>Highways</h3><p>Donec sed nunc in lacus fermentum ultrices ut turpis. Quisque sodales turpis risus dignissim non auctor velit malesuada.</p><span class="btn-small">Read More</span></div>
  <div class="route" style="left:279px;top:58px"><h3>Northline Rail Inter modal</h3><p>Donec sed nunc in lacus fermentum ultrices ut turpis. Quisque sodales turpis risus dignissim non auctor velit malesuada.</p><span class="btn-small">Read More</span></div>
  <div class="route" style="left:543px;top:58px"><h3>Millbrook Airport</h3><p>Donec sed nunc in lacus fermentum ultrices ut turpis. Quisque sodales turpis risus dignissim non auctor velit malesuada.</p><span class="btn-small">Read More</span></div>
</section>

<footer class="site-footer">
  <div class="foot-col" style="left:167px;width:236px"><h4>About Us</h4><p>Lorem Ipsum is simply dummy text of the printing and typesetting industry. Lorem Ipsum has been the industry's standard dummy text.Lorem Ipsum is simply dummy text of the printing and typesetting industry.</p></div>
  <div class="foot-col" style="left:464px"><h4>Our Services</h4><p>voulez utiliser<br>Tous les<br>Lorem Ipsum<br>Contient des<br>Combinaison</p></div>
  <div class="foot-col" style="left:620px"><h4>Contact Us</h4><p>48 Harbor Lane, Suite 310<br>Avondale, MA 01999-2014<br>Ph (555) 201-7734 | TTY (555)</p></div>
  <div class="foot-brand abs"><div class="mark">QRV</div><div class="name">QRV Advisors</div></div>
  <div class="copyright abs">© Copyright 2014</div>
  <div class="foot-social abs"><span></span><span></span><span></span><span></span></div>
</footer>

</body>
</html>
```